Flyer für Immobilien (A4)
Zielgruppe
Es geht um den Verkauf von 2 Immobilien, welche auf diesem Flyer (DIN A4) mit Bildmateriel und kurzem Beschreib vorgestellt werden sollten.
Der Flyer ist für die Verteilung in Briefkästen von Privathaushältern gedacht.
Aufgabenstellung
Auf der Vorderseite sämtliche Texte, das Logo sowie die Aussenansicht der Liegenschaft (Bild 1) platzieren.
Auf der Rückseite können die restlichen Fotos in einer sinnvollen Aufteilung abgebildet werden.
Folgender Text sollte auf der Vorderseite gut aufgeteilt werden:
2x attraktive 4½-Zimmer-Wohnungen mit Balkon und schöner Aussicht ab Fr. 840‘000.—

```html
<!DOCTYPE html>
<html lang="de">
<head>
<meta charset="utf-8">
<title>Flyer Immobilien – Vorder- und Rückseite</title>
<link href="https://fonts.googleapis.com/css2?family=Nunito:wght@400;600;800;900&display=swap" rel="stylesheet">
<style>
  :root {
    --brand: #8b1d57;
    --brand-dark: #6e1544;
    --paper: #ffffff;
    --stage: #dcdcdc;
    --ink: #7a1a4e;
    --muted: #9a4a76;
  }
  * { box-sizing: border-box; margin: 0; padding: 0; }
  html, body { width: 1200px; height: 793px; overflow: hidden; }
  body {
    background: var(--stage);
    font-family: "Nunito", sans-serif;
    position: relative;
  }
  .sheet {
    position: absolute;
    top: 195px;
    width: 570px;
    height: 403px;
    background: var(--paper);
    box-shadow: 0 2px 6px rgba(0,0,0,.12);
    overflow: hidden;
  }
  .sheet--front { left: 20px; }
  .sheet--back { left: 610px; }

  /* Front */
  .hero {
    position: absolute; left: 9px; top: 9px; width: 552px; height: 316px;
    background: linear-gradient(180deg, #3f8fd6 0%, #86bfe8 38%, #e6d99a 58%, #7a9a3a 78%, #5b4a2c 100%);
  }
  .hero-edge { position: absolute; left: 9px; top: 312px; width: 552px; height: 14px; }
  .headline-band { position: absolute; left: 83px; top: 9px; width: 402px; height: 82px; }
  .headline {
    position: absolute; left: 83px; top: 19px; width: 402px;
    color: #fff; font-weight: 900; font-size: 28px; line-height: 25px;
    text-align: center; letter-spacing: .3px; text-transform: uppercase;
  }
  .price-tag {
    position: absolute; left: 420px; top: 170px; width: 150px; height: 38px;
    background: var(--brand); transform: rotate(5deg);
    color: #fff; font-weight: 900; font-size: 16px; line-height: 38px;
    padding-left: 10px; letter-spacing: .5px;
  }
  .brand-mark {
    position: absolute; display: flex; flex-direction: column; align-items: center;
    color: var(--brand); font-weight: 800; text-align: center;
  }
  .brand-mark .dot { width: 12px; height: 12px; border-radius: 50%; background: var(--brand); margin-bottom: 4px; }
  .brand-mark .name { font-size: 9px; line-height: 11px; }
  .brand-mark .sub { font-size: 6.5px; line-height: 8px; font-weight: 600; color: var(--muted); }
  .sheet--front .brand-mark { left: 20px; top: 340px; width: 100px; }
  .divider { position: absolute; left: 133px; top: 338px; width: 1px; height: 54px; background: var(--brand); }
  .offer {
    position: absolute; left: 155px; top: 342px; width: 400px;
    color: var(--brand); font-size: 18px; line-height: 19px; font-weight: 400;
  }
  .offer strong { font-weight: 900; }

  /* Back */
  .photo { position: absolute; }
  .photo--living { left: 9px; top: 9px; width: 273px; height: 165px;
    background: linear-gradient(180deg, #f4f4f2 0%, #e9e7e2 60%, #c9a466 78%, #b88e50 100%); }
  .photo--dining { left: 285px; top: 9px; width: 276px; height: 165px;
    background: linear-gradient(180deg, #f6f6f4 0%, #ecebe7 62%, #cfaa6b 80%, #bb9154 100%); }
  .photo--bedroom { left: 9px; top: 178px; width: 273px; height: 164px;
    background: linear-gradient(180deg, #f3f3f1 0%, #e6e6e4 45%, #8c9098 70%, #8a8583 100%); }
  .floor-plan { position: absolute; left: 373px; top: 178px; width: 188px; height: 218px;
    background: linear-gradient(180deg, #bdb6b6 0%, #aaa2a2 100%); }
  .sheet--back .brand-mark { left: 285px; top: 285px; width: 90px; }
  .contact-rule { position: absolute; left: 9px; top: 350px; width: 380px; height: 1px; background: var(--brand); }
  .contact {
    position: absolute; left: 9px; top: 355px; color: var(--brand);
    font-size: 9.5px; line-height: 12.5px;
  }
  .contact strong { font-weight: 800; }
</style>
</head>
<body>
  <section class="sheet sheet--front" aria-label="Flyer Vorderseite">
    <div class="hero" role="img" aria-label="Aussenansicht des Mehrfamilienhauses mit Balkonen vor blauem Himmel und grünen Hügeln"></div>
    <svg class="hero-edge" viewBox="0 0 552 14" preserveAspectRatio="none" aria-hidden="true">
      <polygon fill="#ffffff" points="0,14 0,6 6,2 12,6 18,2 24,6 30,2 36,6 42,2 48,6 54,2 60,6 66,2 72,6 78,2 84,6 90,2 96,6 102,2 108,6 114,2 120,6 126,2 132,6 138,2 144,6 150,2 156,6 162,2 168,6 174,2 180,6 186,2 192,6 198,2 204,6 210,2 216,6 222,2 228,6 234,2 240,6 246,2 252,6 258,2 264,6 270,2 276,6 282,2 288,6 294,2 300,6 306,2 312,6 318,2 324,6 330,2 336,6 342,2 348,6 354,2 360,6 366,2 372,6 378,2 384,6 390,2 396,6 402,2 408,6 414,2 420,6 426,2 432,6 438,2 444,6 450,2 456,6 462,2 468,6 474,2 480,6 486,2 492,6 498,2 504,6 510,2 516,6 522,2 528,6 534,2 540,6 546,2 552,6 552,14"/>
    </svg>
    <svg class="headline-band" viewBox="0 0 402 82" preserveAspectRatio="none" aria-hidden="true">
      <path d="M0 0 H402 V70 Q300 70 201 80 Q100 70 0 70 Z" fill="var(--brand)"/>
      <path d="M0 72 Q100 72 201 82 Q300 72 402 72" fill="none" stroke="#ffffff" stroke-width="1.5"/>
    </svg>
    <h1 class="headline">Immobilien mit<br>mehr Sonnenseiten</h1>
    <div class="price-tag">ab Fr. 840’000.-</div>

    <div class="brand-mark">
      <span class="dot"></span>
      <span class="name">Brunnhalde &amp; Partner AG</span>
      <span class="sub">Immobilien</span>
    </div>
    <div class="divider"></div>
    <p class="offer"><strong>2x</strong> attraktive <strong>4½</strong>-Zimmer-Wohnungen mit<br>Balkon und schöner Aussicht</p>
  </section>

  <section class="sheet sheet--back" aria-label="Flyer Rückseite">
    <div class="photo photo--living" role="img" aria-label="Wohnzimmer mit grauem Sofa und Parkettboden"></div>
    <div class="photo photo--dining" role="img" aria-label="Essbereich mit Holztisch und offener Küche"></div>
    <div class="photo photo--bedroom" role="img" aria-label="Schlafzimmer mit Doppelbett und Bild an der Wand"></div>
    <div class="floor-plan" role="img" aria-label="Grundriss der 4½-Zimmer-Wohnung mit Schlafzimmern, Bad, Küche, Wohnen, Essen und Balkon"></div>

    <div class="brand-mark">
      <span class="dot"></span>
      <span class="name">Brunnhalde &amp; Partner AG</span>
      <span class="sub">Immobilien</span>
    </div>
    <div class="contact-rule"></div>
    <address class="contact" style="font-style:normal">
      <strong>Brunnhalde &amp; Partner AG</strong> , Lindenweg 12 , 6300 Seeberg<br>
      <strong>Tel.: 041 555 12 34 , Fax: 041 555 12 35</strong><br>
      email: info@brunnhalde-partner.ch
    </address>
  </section>
</body>
</html>
```